email presentation and marketing

we need a email to be used to present our company and services to potential customer. it needs to contain our logo, address, details about our company, photos and a well described text about our work .
I will send a web site from one of the company we are targeting.
The e mail must be sober, elegant, persuasive. The client needs to have the feeling it is dealing to a big company.
See below one of out potential clients
http://qrvdwellings.com/

Target Market(s)

High end custom homes

Industry/Entity Type

Painting And Decorating

Font styles to use
Serif
Sans Serif

Requirements
Must have
• Our name, location, portfolio (need to send some pics), web site http://kb-coatingworks.com.
• Need to develop a email to present our company to potential clients.
Nice to have
• clients reviews.
• we are listed on nest ratings. https://nestratings.com/companies/5831046-kb-custom?service_area=7420561
Should not have
• not colorful

```html
<!DOCTYPE html>
<html lang="en">
<head>
<meta charset="utf-8">
<title>KB Coating Works – Introduction</title>
<link href="https://fonts.googleapis.com/css2?family=Roboto:ital,wght@0,400;0,500;0,700;1,400&display=swap" rel="stylesheet">
<style>
:root{
  --dark:#2c2c30;
  --darker:#232326;
  --footer:#1f1f22;
  --gold:#e3c310;
  --gold-deep:#c9ab06;
  --logo-gold:#d4a72c;
  --paper:#f1f1f1;
  --white:#ffffff;
  --ink:#222222;
  --muted:#555555;
}
*{box-sizing:border-box;margin:0;padding:0}
html,body{width:1200px;height:3285px;overflow:hidden}
body{font-family:"Roboto",Arial,sans-serif;background:var(--dark);color:var(--ink);position:relative}
.abs{position:absolute}

/* header */
.header{left:0;top:0;width:1200px;height:285px;background:var(--dark)}
.brand{left:190px;top:92px;width:320px;text-align:center;color:var(--logo-gold);font-weight:700;font-size:34px;line-height:1.1;letter-spacing:.5px;white-space:nowrap}
.brand .mark{display:block;width:40px;height:40px;background:var(--logo-gold);margin:0 auto 16px}
.contact{right:153px;top:36px;text-align:right;color:var(--gold);font-size:19px;line-height:25px}
.contact p{margin-bottom:23px}
.contact p:last-child{margin:0}

/* hero */
.hero-band{left:0;top:285px;width:1200px;height:515px;background:#3a3a3d}
.side-photo{top:328px;width:92px;height:476px}
.hero-photo{left:92px;top:285px;width:1018px;height:565px;
  background:linear-gradient(180deg,#cfd2d6 0%,#b3b7bc 18%,#8e8a84 30%,#a8a196 45%,#6e6a66 58%,#3d3b3a 64%,#e4e7ea 70%,#f6f7f8 100%);
  box-shadow:0 0 18px rgba(0,0,0,.55)}
.hero-title{left:153px;top:804px;width:902px;height:46px;background:var(--gold);color:var(--ink);font-weight:700;font-size:23px;line-height:46px;text-align:center;letter-spacing:.3px}
.intro{left:150px;top:850px;width:904px;height:256px;background:var(--white);border-radius:0 0 16px 16px;padding:24px 22px;text-align:center;font-size:23px;line-height:36px;color:#2a2a2a}
.btn{width:285px;height:41px;border-radius:21px;background:var(--gold);color:var(--ink);font-weight:500;font-size:21px;line-height:41px;text-align:center;left:458px}

/* services */
.services{left:0;top:1226px;width:1200px;height:246px;background:var(--gold);border-bottom:10px solid var(--gold-deep)}
.service{top:1254px;width:210px;text-align:center}
.service h3{font-size:21px;font-weight:700;margin-bottom:14px;letter-spacing:.3px}
.service .ph{height:139px;border:3px solid var(--white)}

/* testimonials */
.testimonials{left:0;top:1482px;width:1200px;height:822px;background:var(--paper)}
.sec-title{width:1200px;left:0;text-align:center;font-size:26px;font-weight:500}
.review{top:1600px;width:420px;text-align:center}
.avatar{display:block;margin:0 auto 18px}
.review .name{font-size:17px;color:#444;margin-bottom:28px}
.review .role{font-size:14px;color:#444;margin-bottom:22px}
.review .quote{font-size:13px;font-style:italic;color:var(--muted);line-height:17px;padding:0 20px}
.big-photo{top:1861px;width:423px;height:423px}

/* works */
.works-title{top:2326px;color:var(--white)}
.work{top:2396px;width:186px;height:306px}

/* footer */
.footer{left:0;top:2818px;width:1200px;height:401px;background:var(--footer)}
.foot-brand{left:450px;top:2858px;width:300px;text-align:center;color:var(--logo-gold);font-weight:700;font-size:30px;line-height:1.1;white-space:nowrap}
.foot-brand .mark{display:block;width:30px;height:30px;background:var(--logo-gold);margin:0 auto 12px}
.foot-info{left:0;top:2994px;width:1200px;text-align:center;color:var(--white);font-size:19px;line-height:24px}
.social{left:486px;top:3151px;display:flex;gap:17px}
.social span{width:40px;height:40px;border:2px solid #bbb;border-radius:50%}
.legal{left:0;top:3219px;width:1200px;height:66px;background:var(--darker);color:var(--white);text-align:center;font-size:19px;line-height:66px}
</style>
</head>
<body>

<header class="header abs"></header>
<div class="brand abs"><span class="mark"></span>KB Coating Works</div>
<div class="contact abs">
  <p>Ph: 555 836 2190</p>
  <p>A: 82 Birchmount Lane, Unit C7 &nbsp;|&nbsp; K4R 2T9<br>Toronto | Ontario</p>
  <p>info@coatingworksstudio.com<br>http://coatingworksstudio.com/</p>
</div>

<div class="hero-band abs"></div>
<div class="side-photo abs" style="left:0;background:linear-gradient(90deg,#e9e9e9 0%,#f4f4f4 40%,#2a2a2a 55%,#dcdcdc 70%,#bcbcbc 100%)" role="img" aria-label="Interior photo of a white hallway with dark railing"></div>
<div class="side-photo abs" style="left:1108px;background:linear-gradient(90deg,#c9c3bb 0%,#f2f0ed 35%,#ffffff 60%,#d6d0c8 100%)" role="img" aria-label="Interior photo of white columns"></div>
<div class="hero-photo abs" role="img" aria-label="Large stone custom home with a turret in winter snow"></div>
<div class="hero-title abs">KB COATING WORKS – WE ARE ALWAYS READY TO SERVE</div>
<div class="intro abs">K.B Coating Works is a Toronto based company that provides customized home painting, commercial and industrial painting services to Greater Toronto and metropolitan cities. We use modern equipment and superior brand materials to deliver a high-quality work which makes us nothing less then proud.</div>
<div class="btn abs" style="top:1150px">GET A QUOTE</div>

<section class="services abs"></section>
<div class="service abs" style="left:158px"><h3>WALLPAPER</h3><div class="ph" role="img" aria-label="Bedroom with patterned wallpaper" style="background:linear-gradient(180deg,#6f6f72 0%,#b9b9bb 35%,#8a8a8d 55%,#e6e6e6 68%,#1f1f22 85%,#3a3a3d 100%)"></div></div>
<div class="service abs" style="left:383px"><h3>DRYWALL</h3><div class="ph" role="img" aria-label="Worker finishing a drywall ceiling" style="background:linear-gradient(120deg,#d8d8d6 0%,#f3f3f1 45%,#ffffff 65%,#e2ddd6 100%)"></div></div>
<div class="service abs" style="left:609px"><h3>SPRYFINISH</h3><div class="ph" role="img" aria-label="Spray finished feature wall in a dark room" style="background:linear-gradient(90deg,#26262a 0%,#3b3a3c 30%,#d8ccb0 50%,#e8dfc8 62%,#5a5046 80%,#2b2826 100%)"></div></div>
<div class="service abs" style="left:834px"><h3>STAIRCASE</h3><div class="ph" role="img" aria-label="Curved staircase with wrought iron railing" style="background:linear-gradient(135deg,#f4f2f0 0%,#e6e0da 40%,#9c6a52 62%,#6b3a28 80%,#e9e5e1 100%)"></div></div>

<section class="testimonials abs"></section>
<h2 class="sec-title abs" style="top:1518px">CLIENT TESTIMONIALS</h2>

<div class="review abs" style="left:167px">
  <svg class="avatar" width="68" height="68" viewBox="0 0 68 68" aria-hidden="true"><circle cx="34" cy="34" r="34" fill="#111"/><circle cx="34" cy="26" r="10" fill="#fff"/><path d="M15 52c3-10 11-14 19-14s16 4 19 14z" fill="#fff"/></svg>
  <p class="name" style="font-style:italic">ELIO</p>
  <p class="role">Paint Of &nbsp;New Homes and Renovations</p>
  <p class="quote">Marco and his staff are reliable, provide great quality and service. myself and my clients are extremely satisfied with his work.</p>
</div>
<div class="review abs" style="left:613px">
  <svg class="avatar" width="68" height="68" viewBox="0 0 68 68" aria-hidden="true"><circle cx="34" cy="34" r="34" fill="#111"/><circle cx="34" cy="26" r="10" fill="#fff"/><path d="M15 52c3-10 11-14 19-14s16 4 19 14z" fill="#fff"/></svg>
  <p class="name">Brvnbldinc</p>
  <p class="role">Painting Of New Home</p>
  <p class="quote">Contractor was hired to paint New home.<br>Staff was friendly, courteous,<br>helpful, clean, proactive, reliable.</p>
</div>

<div class="big-photo abs" style="left:164px;background:linear-gradient(180deg,#f2f2f2 0%,#8e8e90 14%,#b5b5b7 30%,#6f6f72 48%,#d9d4cf 60%,#25252a 72%,#3b3b40 84%,#4a3a30 100%)" role="img" aria-label="Bedroom with damask wallpaper and upholstered bed"></div>
<div class="big-photo abs" style="left:615px;background:linear-gradient(180deg,#e6e2de 0%,#cfc8c1 22%,#3a3c3a 35%,#6e7a68 55%,#2a2a2a 68%,#cfc9c2 80%,#e4e0db 100%)" role="img" aria-label="Living room with fireplace and tall black windows"></div>

<h2 class="sec-title works-title abs">OUR WORKS</h2>
<div class="work abs" style="left:171px;background:linear-gradient(180deg,#cdbfae 0%,#ece6de 35%,#dcd3c8 55%,#fbfaf8 75%,#e5e0da 100%)" role="img" aria-label="Bathroom with freestanding tub under a domed ceiling"></div>
<div class="work abs" style="left:396px;background:linear-gradient(160deg,#f6f6f6 0%,#e2e2e2 30%,#2b2b2e 50%,#f0f0f0 62%,#1c1c1e 80%,#e8e8e8 100%)" role="img" aria-label="Curved staircase with dark treads"></div>
<div class="work abs" style="left:622px;background:linear-gradient(180deg,#3a2e26 0%,#c9bcae 25%,#e6ddd2 45%,#6a4a36 65%,#2e2018 100%)" role="img" aria-label="Long hallway with dark wood floor"></div>
<div class="work abs" style="left:847px;background:linear-gradient(180deg,#f1f1f1 0%,#a8a49f 25%,#7d7770 45%,#4a4540 62%,#efefef 75%,#5a4234 100%)" role="img" aria-label="Stone fireplace with built-in shelves"></div>
<div class="btn abs" style="top:2746px">GET A QUOTE</div>

<footer class="footer abs"></footer>
<div class="foot-brand abs"><span class="mark"></span>KB Coating Works</div>
<div class="foot-info abs">
  KB Coating Works<br>Contact: Marco Ferreira<br>555 274 6190|kbcoatingworks12@mailbox.com<br>kb-coatingworks.com
</div>
<div class="social abs" aria-label="Social links"><span></span><span></span><span></span><span></span><span></span></div>
<div class="legal abs">KB Coating Works © All rights reserved</div>

</body>
</html>
```